Card Design for my dog training business Brightpaw Obedience

Need a business card design for my dog training business with my new logo. Want the card to come off professional yet fun. Want it to be very eye catchy as well. I normally have these at vet clinics, pet stores, and groomers. so need it to look better than my competitors.
Target Market(s)
dog owners
Industry/Entity Type
Dog Training
Contact Information for Business Card
needs logo, my name and info
Font styles to use
Serif
Colors
0255a3
ffffff
ec1f27
000000
333333
fbfbfb
Requirements
Must have
- Brightpaw Obedience
- Felix Orland
- 415 903 2276
- info@brightpawobedience.example
- www.brightpawobedience.example

```html
<!DOCTYPE html>
<html lang="en">
<head>
<meta charset="utf-8">
<title>Brightpaw Obedience – Business Card</title>
<link rel="stylesheet" href="https://fonts.googleapis.com/css2?family=EB+Garamond:ital,wght@0,500;1,400&family=Open+Sans:wght@400;700&display=swap">
<style>
  :root {
    --stage: #2a2a2a;
    --card-dark: #2f2d2e;
    --card-dark-edge: #1f1d1e;
    --paper: #ffffff;
    --ink: #000000;
    --ink-soft: #333333;
    --rule: #9a9a9a;
    --band-edge: #555555;
    --light: #fbfbfb;
  }
  * { margin: 0; padding: 0; box-sizing: border-box; }
  html, body { width: 1200px; height: 892px; overflow: hidden; }
  body {
    background: var(--stage);
    position: relative;
    font-family: "Open Sans", sans-serif;
  }
  .card {
    position: absolute;
    top: 292px;
    width: 540px;
    height: 309px;
    overflow: hidden;
    box-shadow: 0 10px 30px rgba(0,0,0,.5);
  }
  /* Back side */
  .card--back {
    left: 40px;
    background: radial-gradient(ellipse at 50% 40%, var(--card-dark) 0%, var(--card-dark-edge) 100%);
    color: var(--light);
  }
  .brand-mark {
    position: absolute;
    left: 0; right: 0; top: 96px;
    display: flex; align-items: center; justify-content: center; gap: 12px;
    font-family: "EB Garamond", serif;
    font-weight: 500;
    font-size: 38px;
    color: var(--light);
  }
  .brand-mark__square {
    width: 22px; height: 22px;
    background: var(--light);
  }
  .tagline {
    position: absolute;
    left: 0; right: 0; bottom: 46px;
    text-align: center;
    font-family: "EB Garamond", serif;
    font-style: italic;
    font-size: 15px;
    color: var(--light);
  }
  /* Front side */
  .card--front {
    left: 620px;
    background: var(--paper);
    color: var(--ink);
  }
  .front-logo {
    position: absolute;
    right: 34px; top: 40px;
    display: flex; align-items: center; gap: 8px;
    font-family: "EB Garamond", serif;
    font-weight: 500;
    font-size: 22px;
    color: var(--ink);
  }
  .front-logo__square {
    width: 14px; height: 14px;
    background: var(--ink);
  }
  .front-rule {
    position: absolute;
    left: 200px; right: 22px; top: 112px;
    height: 1px; background: var(--rule);
  }
  .holder-name {
    position: absolute;
    left: 28px; top: 178px;
    font-weight: 700;
    font-size: 19px;
    color: var(--ink);
  }
  .name-rule {
    position: absolute;
    left: 28px; width: 250px; top: 210px;
    height: 1px; background: var(--rule);
  }
  .contact-list {
    position: absolute;
    left: 30px; top: 218px;
    list-style: none;
    font-size: 12.5px;
    color: var(--ink-soft);
    line-height: 20px;
  }
  .contact-list li { display: flex; align-items: center; gap: 8px; }
  .contact-list svg { width: 13px; height: 13px; fill: var(--ink); }
  .front-band {
    position: absolute; left: 0; bottom: 0;
    width: 540px; height: 60px;
  }
  .website {
    position: absolute;
    left: 30px; bottom: 6px;
    font-size: 13.5px;
    color: var(--paper);
  }
</style>
</head>
<body>
  <section class="card card--back" aria-label="Card back">
    <div class="brand-mark">
      <span class="brand-mark__square" aria-hidden="true"></span>
      <span>Brightpaw Obedience</span>
    </div>
    <p class="tagline">“Teaching good manners to every dog, one step at a time.”</p>
  </section>

  <section class="card card--front" aria-label="Card front">
    <div class="front-logo">
      <span class="front-logo__square" aria-hidden="true"></span>
      <span>Brightpaw Obedience</span>
    </div>
    <div class="front-rule"></div>

    <h1 class="holder-name">Felix Orland</h1>
    <div class="name-rule"></div>
    <ul class="contact-list">
      <li>
        <svg viewBox="0 0 16 16" aria-hidden="true"><path d="M2 5c0-2 2-3 6-3s6 1 6 3v1h-3V5H5v1H2zM4 7h8l2 7H2z"/></svg>
        415 903 2276
      </li>
      <li>
        <svg viewBox="0 0 16 16" aria-hidden="true"><path d="M1 3h14v2L8 9 1 5zM1 7l7 4 7-4v6H1z"/></svg>
        info@brightpawobedience.example
      </li>
    </ul>

    <svg class="front-band" viewBox="0 0 540 60" aria-hidden="true">
      <polygon points="0,32 322,32 338,12 540,12 540,60 0,60" fill="var(--ink)"/>
      <polygon points="326,32 342,14 540,14 540,16 343,16 328,34" fill="var(--band-edge)"/>
    </svg>
    <p class="website">www.brightpawobedience.example</p>
  </section>
</body>
</html>
```